Design a Website in Wordpress for an Australian Health Training Company in Health related courses

We require a WORDPRESS based Website (due to add on's we need to use for third party software) to replace our old site.
We offer national face to face delivery in medical reception, terminology and also administration.
The website will have around 6 pages and the ability to describe our main 6 courses (perhaps on the Courses page this may be tabs opening up to details for example?)
I have attached a previous sample of a Joomla site which was being developed (please do not feel you have to copy this - but I am just giving it as a sample - copying would be boring). But it gives an idea of look/feel and colours which may be suitable. Open to other ideas though.
I will provide some of the content, but would like the ability to finish the content myself.
Images and graphics are important. While a few medical photos re great - don't be tempted to us all pictures of doctors and nurses (although a couple would be good) - these are administrative courses so general corporate, eye catching visionary pictures of people in general are great. A medical type picture is also fine.
THE BOOKING system - will be via an ADD ON which will occur at the end of the project and is supplied by a third party software company (our student management system). This project will include up to 2 hours working with the Tech guys from the third party software to enable the ADD ON. If this ADD ON requires more time, we will pay hourly (although I do not expect it will).
Target Market(s)
Mostly a female market, many mature aged women target 25-45 yrs. Mixture of medical/health and corporate. Maybe a bit of mums returning to work and corporate inspiration.
Industry/Entity Type
It Company
Coding
Coded - Design and coding required
Number of Pages Required
5+ page
Requirements
Must have
- Wordpress
- Great graphics
- Interesting
- professional and clean
- Enquiry section (info Pak)
- Should have a University feel to it - Education
- Pages
- Home Page - About Us - Recruitment -Courses - Class Schedule - Traineeships Queensland Funding - Latest News Blog - Corporate Training- Contact us

```html
<!DOCTYPE html>
<html lang="en">
<head>
<meta charset="utf-8">
<title>Harbourline Institute of Training</title>
<link rel="stylesheet" href="https://fonts.googleapis.com/css2?family=Mulish:wght@300;400;600;700&display=swap">
<style>
:root{
  --navy:#1b2a57;
  --navy-deep:#0f1c44;
  --card:#1f2a4a;
  --blue:#1d4f9c;
  --blue-text:#2a5599;
  --orange:#f68f38;
  --orange-dark:#e87a20;
  --grey-text:#555b66;
  --light:#f2f2f2;
  --line:#d8d8d8;
  --white:#ffffff;
}
*{box-sizing:border-box;margin:0;padding:0}
html,body{width:1200px;height:2821px;overflow:hidden}
body{font-family:"Mulish",Arial,sans-serif;color:var(--grey-text);background:var(--white);position:relative}
section,header,footer{position:absolute;left:0;width:1200px}
.abs{position:absolute}
.btn{position:absolute;display:flex;align-items:center;justify-content:center;border-radius:5px;font-size:11px;letter-spacing:.5px;text-transform:uppercase;color:var(--white);font-weight:600;white-space:nowrap}
.btn-navy{background:linear-gradient(#2c3a63,var(--navy-deep))}
.btn-orange{background:linear-gradient(#f9a050,var(--orange-dark))}

/* top bar */
.topbar{top:0;height:38px;background:linear-gradient(90deg,var(--navy-deep),#1a3a86 50%,var(--navy-deep))}
.topbar .connect{left:290px;top:12px;font-size:10px;color:var(--white)}
.topbar .search{left:600px;top:9px;width:207px;height:22px;border:1px solid #5670b0;background:#0d1a40;border-radius:3px;font-size:10px;color:#c9d2ea;padding:4px 8px}
.topbar .search svg{position:absolute;right:6px;top:5px}
.topbar .funding{left:812px;top:9px;width:198px;height:22px;background:linear-gradient(#3f6ec2,#2a55a3);border-radius:3px;font-size:9.5px;color:var(--white);display:flex;align-items:center;justify-content:center;text-transform:uppercase;letter-spacing:.2px;white-space:nowrap}

/* header */
.site-header{top:38px;height:88px;background:var(--white);border-bottom:1px solid var(--line)}
.brand{left:188px;top:-12px;width:104px;height:110px;background:var(--white);box-shadow:0 2px 6px rgba(0,0,0,.15);display:flex;align-items:center;justify-content:center;text-align:center;font-size:11px;font-weight:700;color:var(--navy);line-height:1.3;padding:8px;z-index:3}
.nav{left:0;top:0;width:1200px;height:88px}
.nav-item{position:absolute;top:46px;transform:translate(-50%,-50%);font-size:9.5px;color:#3c4250;text-transform:uppercase;text-align:center;line-height:1.3;white-space:nowrap}
.nav .home{width:14px;height:14px;display:block}
.enroll{left:914px;top:14px;width:96px;height:24px;background:linear-gradient(#8f9196,#6c6e73);border-radius:3px;font-size:9.5px;color:var(--white);display:flex;align-items:center;justify-content:center;gap:6px;text-transform:uppercase;white-space:nowrap}
.infopack{left:914px;top:44px;width:96px;height:26px;background:linear-gradient(#f9a050,var(--orange-dark));border-radius:3px;font-size:9.5px;color:var(--white);display:flex;align-items:center;justify-content:center;gap:6px;text-transform:uppercase;white-space:nowrap}

/* hero */
.hero{top:126px;height:433px}
.hero-photo{position:absolute;inset:0;background:linear-gradient(90deg,#e8e4e0 0%,#f1f1f0 35%,#eef2f4 60%,#f6f7f8 100%)}
.hero h1{position:absolute;right:196px;top:128px;font-size:30px;font-weight:400;color:var(--blue-text)}
.hero p{position:absolute;right:196px;top:178px;width:465px;text-align:right;font-size:11px;line-height:20px;color:#6b707a}
.hero .btn{left:845px;top:263px;width:163px;height:33px;font-size:10px}
.hero .dots{position:absolute;left:1164px;top:193px;display:flex;flex-direction:column;gap:9px}
.hero .dots span{width:13px;height:13px;border:1.5px solid var(--orange);border-radius:50%;background:var(--white)}
.hero .dots span.on{background:var(--navy);box-shadow:inset 0 0 0 3px var(--white)}

/* course icons */
.course-strip{top:559px;height:161px;background:linear-gradient(#fbfbfb,#ececec);border-top:1px solid var(--line);border-bottom:1px solid var(--line)}
.course{position:absolute;top:30px;width:170px;margin-left:-85px;text-align:center;font-size:14px;line-height:22px;color:#4e5462}
.course svg{display:block;margin:0 auto 12px}

/* welcome */
.welcome{top:720px;height:380px;text-align:center}
.welcome h2{position:absolute;top:84px;width:100%;font-size:20px;font-weight:400;color:var(--navy);letter-spacing:.5px}
.welcome p{position:absolute;left:190px;width:820px;font-size:11px;line-height:22.5px;color:#4a4f5a}
.welcome .btn{left:519px;top:286px;width:162px;height:34px}

/* why */
.why{top:1100px;height:486px;border-top:1px solid var(--line)}
.why-photo{position:absolute;inset:0;background:linear-gradient(90deg,#c9c9c9,#ececec 30%,#e0e0e0 70%,#bfbfbf)}
.why h2{position:absolute;top:46px;width:100%;text-align:center;font-size:20px;font-weight:400;color:var(--navy);letter-spacing:.5px}
.card{position:absolute;top:138px;width:254px;height:263px;background:var(--card);border-radius:5px;text-align:center;color:var(--white)}
.card .badge{position:absolute;left:89px;top:-25px}
.card h3{position:absolute;top:84px;width:100%;font-size:20px;font-weight:400}
.card p{position:absolute;top:126px;left:26px;width:202px;font-size:11px;line-height:18px;color:#dfe3ee}
.why .dots{position:absolute;left:566px;top:433px;display:flex;gap:7px}
.why .dots span{width:9px;height:9px;border-radius:50%;background:var(--navy)}
.why .dots span.on{background:var(--white)}

/* info pack form */
.infoform{top:1586px;height:327px;background:var(--orange)}
.infoform h2{position:absolute;top:78px;width:100%;text-align:center;font-size:20px;font-weight:400;color:var(--white);letter-spacing:1px}
.field{position:absolute;height:32px;border:1.5px solid #fbc598;border-radius:2px;font-size:10.5px;color:#fde3cc;padding:8px 10px}
.field .caret{position:absolute;right:9px;top:13px;width:0;height:0;border-left:4px solid transparent;border-right:4px solid transparent;border-top:5px solid var(--white)}
.infoform .btn{left:519px;top:250px;width:162px;height:32px}

/* testimonials */
.testimonials{top:1913px;height:373px}
.testimonials h2{position:absolute;top:42px;width:100%;text-align:center;font-size:20px;font-weight:400;color:var(--blue-text);letter-spacing:.5px}
.quote-box{position:absolute;left:201px;top:147px;width:800px;height:131px;border:1px solid #b9bcc2;border-radius:6px;background:var(--white)}
.quote-box p{position:absolute;left:22px;top:48px;width:756px;text-align:center;font-size:11px;line-height:18px;color:#4a4f5a}
.pointer{position:absolute;left:590px;top:277px}
.avatar{position:absolute;left:561px;top:96px}
.testimonials .name{position:absolute;top:300px;width:100%;text-align:center;font-size:16px;color:var(--blue-text)}
.arrow{position:absolute;top:202px}

/* enquiry band */
.enquiry{top:2286px;height:285px}
.enquiry-photo{position:absolute;inset:0;background:linear-gradient(90deg,#173f8a,#2a5eb3 45%,#2457a8 70%,#163a80)}
.enquiry p{position:absolute;left:295px;top:94px;width:610px;text-align:center;font-size:14.5px;line-height:25.5px;color:var(--white)}
.enquiry .btn{left:519px;top:193px;width:162px;height:34px}

/* footer */
.site-footer{top:2571px;height:250px;background:var(--white)}
.foot-brand{left:188px;top:30px;width:109px;height:108px;display:flex;align-items:center;justify-content:center;text-align:center;font-size:11px;font-weight:700;color:var(--navy);line-height:1.3}
.foot-col{position:absolute;top:30px}
.foot-col h4{font-size:11px;font-weight:600;color:var(--orange);margin-bottom:12px}
.foot-col li{list-style:none;font-size:9.5px;line-height:18px;color:#4a4f5a;padding-left:14px;position:relative;white-space:nowrap}
.foot-col li::before{content:"";position:absolute;left:2px;top:7px;width:4px;height:4px;border-right:1px solid #888;border-top:1px solid #888;transform:rotate(45deg)}
.foot-bottom{position:absolute;top:213px;left:0;width:1200px;height:37px;border-top:1px solid var(--line);font-size:9.5px;color:#555}
.foot-bottom .copy{position:absolute;left:203px;top:13px}
.foot-bottom .legal{position:absolute;right:197px;top:13px}
</style>
</head>
<body>

<header class="topbar">
  <div class="abs connect">Connect With Us</div>
  <div class="abs search">Search
    <svg width="11" height="11" viewBox="0 0 12 12"><circle cx="5" cy="5" r="3.6" fill="none" stroke="#fff" stroke-width="1.5"/><path d="M7.8 7.8l3 3" stroke="#fff" stroke-width="1.6"/></svg>
  </div>
  <div class="abs funding">Traineeships Queensland Funding</div>
</header>

<header class="site-header">
  <div class="abs brand">HARBOURLINE INSTITUTE OF TRAINING</div>
  <nav class="abs nav">
    <span class="nav-item" style="left:347px"><svg class="home" viewBox="0 0 14 14"><path d="M1 7L7 1.5 13 7h-2v5.5H8.5V9h-3v3.5H3V7z" fill="#2a55a3"/></svg></span>
    <span class="nav-item" style="left:396px">About Us</span>
    <span class="nav-item" style="left:471px">Recruitment</span>
    <span class="nav-item" style="left:546px">Courses</span>
    <span class="nav-item" style="left:623px">Class<br>Schedule</span>
    <span class="nav-item" style="left:702px">Latest<br>News Blog</span>
    <span class="nav-item" style="left:777px">Corporate<br>Training</span>
    <span class="nav-item" style="left:856px">Contact Us</span>
  </nav>
  <div class="abs enroll"><svg width="9" height="11" viewBox="0 0 9 11"><path d="M0 0h6l3 3v8H0z" fill="#fff"/></svg>Enroll Now</div>
  <div class="abs infopack"><svg width="10" height="10" viewBox="0 0 10 10"><circle cx="5" cy="5" r="4.5" fill="#fff"/><path d="M3 5h4M5.5 3.5L7 5 5.5 6.5" stroke="#e87a20" stroke-width="1.2" fill="none"/></svg>Info Pack</div>
</header>

<section class="hero">
  <div class="hero-photo" role="img" aria-label="Smiling medical professional in a white coat with a stethoscope, soft clinic background"></div>
  <h1>Harbourline Institute Of Training</h1>
  <p>Lorem ipsum dolor sit amet, consectetur adipiscing elit, sed do eiusmod tempor incididunt ut labore et dolore magna aliqua. Ut enim ad minim veniam, quis nostrud exercitation ullamco laboris nisi ut aliquip ex ea commodo consequat.</p>
  <div class="btn btn-navy">Learn More About Us</div>
  <div class="dots"><span class="on"></span><span></span><span></span><span></span></div>
</section>

<section class="course-strip">
  <div class="course" style="left:273px">
    <svg width="34" height="34" viewBox="0 0 34 34" fill="none" stroke="#f68f38" stroke-width="2"><ellipse cx="17" cy="17" rx="14" ry="6"/><ellipse cx="17" cy="17" rx="14" ry="6" transform="rotate(60 17 17)"/><ellipse cx="17" cy="17" rx="14" ry="6" transform="rotate(-60 17 17)"/><circle cx="17" cy="17" r="2" fill="#f68f38"/></svg>
    Medical<br>Reception &amp; Terminology</div>
  <div class="course" style="left:446px">
    <svg width="34" height="34" viewBox="0 0 34 34" fill="none" stroke="#f68f38" stroke-width="2"><path d="M9 3v9a6 6 0 0 0 12 0V3"/><path d="M15 18v5a6 6 0 0 0 12 0v-4"/><circle cx="27" cy="16" r="3"/></svg>
    Cert III Business<br>Administration</div>
  <div class="course" style="left:574px">
    <svg width="34" height="34" viewBox="0 0 34 34"><rect x="3" y="5" width="16" height="10" rx="5" transform="rotate(35 11 10)" fill="#f68f38"/><circle cx="25" cy="23" r="7" fill="none" stroke="#f68f38" stroke-width="2"/><circle cx="11" cy="26" r="4" fill="#f68f38"/></svg>
    Medical<br>Terminology</div>
  <div class="course" style="left:703px">
    <svg width="38" height="34" viewBox="0 0 38 34" fill="none" stroke="#f68f38" stroke-width="2"><rect x="2" y="8" width="34" height="18" rx="2"/><path d="M7 14h2M12 14h2M17 14h2M22 14h2M27 14h2M10 20h18"/></svg>
    Keyboard<br>&amp; Typing</div>
  <div class="course" style="left:841px">
    <svg width="38" height="34" viewBox="0 0 38 34" fill="none" stroke="#f68f38" stroke-width="2"><rect x="6" y="6" width="26" height="17" rx="1"/><path d="M2 27h34"/></svg>
    Harbourline<br>Online</div>
  <div class="course" style="left:950px">
    <svg width="38" height="34" viewBox="0 0 38 34"><path d="M14 6h10v5" fill="none" stroke="#f68f38" stroke-width="2"/><rect x="3" y="10" width="32" height="21" rx="3" fill="#f68f38"/><path d="M19 15v11M13.5 20.5h11" stroke="#fff" stroke-width="3"/></svg>
    Confidentiality</div>
</section>

<section class="welcome">
  <h2>WELCOME TO HARBOURLINE INSTITUTE OF TRAINING</h2>
  <p style="top:138px">Harbourline is Australia's Leading Provider of Educational, Training and Support Services for the Medical and Dental industry - enabling students to be immediately skilled and "Job Ready" for a career in Health. Harbourline is a Registered Training Organisation offering specialised Medical Administration Training in over 15 locations Australia wide. Harbourline have trained thousands of students the required knowledge and skills to become successful health care administrators.</p>
  <p style="top:231px">Our unique Short Medical Reception and Terminology Course and our Full Qualification is Nationally Accredited and the go-to recognised qualification in industry.</p>
  <div class="btn btn-navy">Contact Us</div>
</section>

<section class="why">
  <div class="why-photo" role="img" aria-label="Soft greyscale classroom scene with students and a presenter"></div>
  <h2>WHY HARBOURLINE INSTITUTE ?</h2>

  <div class="card" style="left:201px">
    <svg class="badge" width="76" height="86" viewBox="0 0 76 86"><path d="M2 2h72v50L38 84 2 52z" fill="#e27a22"/><path d="M8 6h60v44L38 78 8 50z" fill="#f68f38"/><circle cx="38" cy="36" r="12" fill="none" stroke="#fff" stroke-width="2"/><path d="M31 46l-4 14 6-3 3 5 2-14M45 46l4 14-6-3-3 5-2-14" fill="none" stroke="#fff" stroke-width="2"/></svg>
    <h3>Quality</h3>
    <p>Harbourline delivery quality, effective training facilitated by industry leaders. Just ask our students who rate us on average of 4.7 out of 5.</p>
  </div>
  <div class="card" style="left:472px">
    <svg class="badge" width="76" height="86" viewBox="0 0 76 86"><path d="M2 2h72v50L38 84 2 52z" fill="#e27a22"/><path d="M8 6h60v44L38 78 8 50z" fill="#f68f38"/><rect x="22" y="24" width="32" height="24" rx="2" fill="none" stroke="#fff" stroke-width="2"/><circle cx="32" cy="33" r="4" fill="none" stroke="#fff" stroke-width="2"/><path d="M26 44c1-4 11-4 12 0M41 31h9M41 36h9M41 41h6" stroke="#fff" stroke-width="2" fill="none"/></svg>
    <h3>Experience</h3>
    <p>Harbourline delivery quality, effective training facilitated by industry leaders. Just ask our students who rate us on average of 4.7 out of 5.</p>
  </div>
  <div class="card" style="left:747px">
    <svg class="badge" width="76" height="86" viewBox="0 0 76 86"><path d="M2 2h72v50L38 84 2 52z" fill="#e27a22"/><path d="M8 6h60v44L38 78 8 50z" fill="#f68f38"/><circle cx="38" cy="37" r="14" fill="none" stroke="#fff" stroke-width="2"/><circle cx="38" cy="37" r="7" fill="none" stroke="#fff" stroke-width="2"/><path d="M34 37l3 3 5-6" stroke="#fff" stroke-width="2" fill="none"/></svg>
    <h3>Value</h3>
    <p>Harbourline delivery quality, effective training facilitated by industry leaders. Just ask our students who rate us on average of 4.7 out of 5.</p>
  </div>
  <div class="dots"><span class="on"></span><span></span><span></span><span></span></div>
</section>

<section class="infoform">
  <h2>EMAIL ME AN INFO PACK</h2>
  <div class="field" style="left:190px;top:139px;width:267px">Name</div>
  <div class="field" style="left:466px;top:139px;width:268px">Email</div>
  <div class="field" style="left:743px;top:139px;width:267px">Course<span class="caret"></span></div>
  <div class="field" style="left:190px;top:190px;width:404px">State<span class="caret"></span></div>
  <div class="field" style="left:606px;top:190px;width:404px">Mobile</div>
  <div class="btn btn-navy">Submit</div>
</section>

<section class="testimonials">
  <h2>TESTIMONIALS</h2>
  <div class="quote-box">
    <p>I completed the course on Feb 13th. Loved it. The trainers, Mara and Lyn were excellent in their delivery and knowledge. I want to say a huge thank you for the course and knowledge I came away with. I have secured a fantastic job after my first application! Such good value for money too! I would highly recommend it. I m a mature age person so its never too late to up -skill yourself to get what you deserve!</p>
  </div>
  <svg class="pointer" width="22" height="13" viewBox="0 0 22 13"><path d="M0 0L11 12 22 0" fill="#fff" stroke="#b9bcc2"/><path d="M1 0h20" stroke="#fff" stroke-width="2"/></svg>
  <svg class="avatar" width="76" height="90" viewBox="0 0 76 90"><path d="M2 2h72v56L38 88 2 58z" fill="#f68f38"/><path d="M7 6h62v50L38 82 7 56z" fill="#c9a88f" role="img" aria-label="Portrait photo of the reviewer"/></svg>
  <div class="name">Jane Porter</div>
  <svg class="arrow" style="left:82px" width="14" height="24" viewBox="0 0 14 24"><path d="M12 1L2 12l10 11" fill="none" stroke="#444" stroke-width="2"/></svg>
  <svg class="arrow" style="left:1104px" width="14" height="24" viewBox="0 0 14 24"><path d="M2 1l10 11L2 23" fill="none" stroke="#444" stroke-width="2"/></svg>
</section>

<section class="enquiry">
  <div class="enquiry-photo" role="img" aria-label="Blue-tinted lecture hall with students seen from behind"></div>
  <p>Lorem ipsum dolor sit amet, consectetur adipiscing elit, sed do eiusmod tempor incididunt ut labore et dolore magna aliqua. Ut enim ad minim veniam, quis nostrud exercitation ullamco laboris nisi ut aliquip ex ea commodo consequat.</p>
  <div class="btn btn-orange">Enquiry</div>
</section>

<footer class="site-footer">
  <div class="abs foot-brand">HARBOURLINE INSTITUTE OF TRAINING</div>
  <div class="foot-col" style="left:344px">
    <h4>Quick Links</h4>
    <ul><li>Home Page</li><li>About Us</li><li>Recruitment</li><li>Class Schedule</li><li>Traineeships Queensland Funding</li><li>Latest News Blog</li><li>Corporate Training</li></ul>
  </div>
  <div class="foot-col" style="left:530px">
    <h4>Course Information</h4>
    <ul><li>Medical Course Overview &amp; Fees</li><li>Medical Course Content</li><li>Testimonials</li><li>Medical Career Prospects</li><li>Book Online</li><li>Contact Us</li><li>Recruitment</li></ul>
  </div>
  <div class="foot-col" style="left:726px">
    <h4>Other Links</h4>
    <ul><li>Medical Reception Training</li><li>Medical Terminology Training</li><li>Medical Computing Training</li><li>Dental Assisting Training</li></ul>
  </div>
  <div class="foot-col" style="left:910px">
    <h4>Course Information</h4>
    <ul><li>Queensland</li><li>Victoria</li><li>New South Wales</li><li>South Australia</li><li>Western Australia</li><li>NT</li></ul>
  </div>
  <div class="foot-bottom">
    <span class="copy">© 2016 Company Name | All Rights Reserved</span>
    <span class="legal">Terms Of Service | Privacy Policy</span>
  </div>
</footer>

</body>
</html>
```